Veltrano.co - Polar Expeditions Specialists

We need a modern, visually striking business card for Veltrano.co, a company specialized in selling expedition cruises to the most remote regions on Earth, with a focus on the Arctic and Antarctica. The design should instantly communicate that the cardholder is an expert in polar travel. Use clean, premium aesthetics with cool tones like icy blue and white, possibly incorporating polar imagery (ice, glaciers, penguins, etc.)

Attached the logo

Contact Information for Business Card

Feels high-end and trustworthy.. Visually memorable — encourages people to keep it

Colors
0054AA
0677BA
7BADD7
CADEEF
E8F1F8

Requirements
Must have
• ice, glaciers, penguins, montains
Nice to have
• modern, transparente,

```html
<!DOCTYPE html>
<html lang="en">
<head>
<meta charset="UTF-8">
<title>Veltrano.co – Business Card</title>
<link href="https://fonts.googleapis.com/css2?family=Poppins:wght@400;500;600;700&display=swap" rel="stylesheet">
<style>
  :root {
    --stage: #6e6e6e;
    --brand-blue: #2f6fb8;
    --deep-blue: #0054aa;
    --mid-blue: #0677ba;
    --sky-blue: #7badd7;
    --pale-blue: #cadeef;
    --ice-white: #e8f1f8;
    --white: #ffffff;
  }
  * { margin: 0; padding: 0; box-sizing: border-box; }
  html, body {
    width: 1093px; height: 1200px; overflow: hidden;
    background: var(--stage);
    font-family: "Poppins", sans-serif;
  }
  .canvas { position: relative; width: 1093px; height: 1200px; }

  .card {
    position: absolute; left: 265px; width: 579px; height: 357px;
    border-radius: 24px; overflow: hidden;
  }
  .card--front { top: 226px; }
  .card--back  { top: 621px; }

  .card__scene { position: absolute; inset: 0; }
  .card--front .card__scene {
    background:
      radial-gradient(ellipse 55% 70% at 30% 85%, #cfe2f1 0%, rgba(207,226,241,0) 70%),
      linear-gradient(115deg, #c7dcee 0%, #e3eef8 45%, #f4f8fc 75%, #eef4fa 100%);
  }
  .card--back .card__scene {
    background:
      radial-gradient(ellipse 35% 55% at 52% 45%, rgba(150,190,228,0.55) 0%, rgba(150,190,228,0) 70%),
      linear-gradient(180deg, #4a86c4 0%, #5b93cc 55%, #4c86c2 75%, #3f78b8 100%);
  }

  .brand { position: absolute; text-align: center; font-weight: 700; }
  .brand__mark { display: block; margin: 0 auto; border-radius: 50%; }
  .brand__name { display: block; letter-spacing: 0.2px; line-height: 1; }
  .brand__tagline { display: block; font-weight: 500; }

  .card--front .brand { left: 40px; top: 26px; width: 240px; color: var(--brand-blue); }
  .card--front .brand__mark { width: 72px; height: 72px; margin-bottom: 24px; background: var(--brand-blue); }
  .card--front .brand__name { font-size: 38px; }
  .card--front .brand__tagline { font-size: 12.5px; font-weight: 600; margin-top: 7px; }

  .card--back .brand { left: 0; right: 0; top: 84px; color: var(--white); }
  .card--back .brand__mark { width: 90px; height: 90px; margin-bottom: 28px; background: var(--white); }
  .card--back .brand__name { font-size: 50px; }
  .card--back .brand__tagline { font-size: 16px; margin-top: 8px; letter-spacing: 0.3px; }

  .contact { position: absolute; left: 304px; top: 130px; color: var(--brand-blue); }
  .contact__name { font-size: 23px; font-weight: 600; line-height: 1.1; }
  .contact__role { font-size: 16.5px; font-weight: 400; line-height: 1.1; }
  .contact__list { list-style: none; margin-top: 15px; }
  .contact__item {
    display: flex; align-items: center; gap: 6px;
    font-size: 16.5px; line-height: 21px;
  }
  .contact__icon { width: 16px; height: 16px; fill: var(--brand-blue); flex: none; }
  .contact__address { font-size: 16.5px; line-height: 21px; margin-top: 12px; }
</style>
</head>
<body>
<main class="canvas">

  <section class="card card--front">
    <div class="card__scene" role="img" aria-label="Photograph of a towering white glacier iceberg under a pale sky"></div>
    <div class="brand">
      <span class="brand__mark" aria-hidden="true"></span>
      <span class="brand__name">Veltrano.co</span>
      <span class="brand__tagline">Polar Expeditions Specialists</span>
    </div>
    <div class="contact">
      <p class="contact__name">Marcus Ellery</p>
      <p class="contact__role">Managing Director</p>
      <ul class="contact__list">
        <li class="contact__item">
          <svg class="contact__icon" viewBox="0 0 24 24" aria-hidden="true"><path d="M6.6 10.8a15.1 15.1 0 0 0 6.6 6.6l2.2-2.2a1 1 0 0 1 1-.25 11.4 11.4 0 0 0 3.6.57 1 1 0 0 1 1 1V20a1 1 0 0 1-1 1A17 17 0 0 1 3 4a1 1 0 0 1 1-1h3.5a1 1 0 0 1 1 1c0 1.25.2 2.45.57 3.57a1 1 0 0 1-.25 1z"/></svg>
          <span>044-987 321 654</span>
        </li>
        <li class="contact__item">
          <svg class="contact__icon" viewBox="0 0 24 24" aria-hidden="true"><path d="M2 5h20v14H2z M3 6l9 7 9-7" fill="var(--brand-blue)" stroke="var(--ice-white)" stroke-width="1.2"/></svg>
          <span>hello@veltrano.co</span>
        </li>
        <li class="contact__item">
          <svg class="contact__icon" viewBox="0 0 24 24" aria-hidden="true"><circle cx="12" cy="12" r="9.5" fill="none" stroke="var(--brand-blue)" stroke-width="2"/><ellipse cx="12" cy="12" rx="4" ry="9.5" fill="none" stroke="var(--brand-blue)" stroke-width="1.6"/><path d="M3 9h18M3 15h18" stroke="var(--brand-blue)" stroke-width="1.6"/></svg>
          <span>www.veltrano.co</span>
        </li>
      </ul>
      <p class="contact__address">18, Harbour Quay Road<br>70213, Norland</p>
    </div>
  </section>

  <section class="card card--back">
    <div class="card__scene" role="img" aria-label="Blue-tinted photograph of an iceberg rising from calm polar water"></div>
    <div class="brand">
      <span class="brand__mark" aria-hidden="true"></span>
      <span class="brand__name">Veltrano.co</span>
      <span class="brand__tagline">Polar Expeditions Specialists</span>
    </div>
  </section>

</main>
</body>
</html>
```